U.S. Popcorn company needs business cards

We are a popcorn company that manufactures popcorn and sells it to grocery stores worldwide. Our theme is "Americana" and our logo is U.S. route 66 which is the most famous highway in the U.S.

We would like the design to be simple and to use both sides. On the back side we would like to see just the logo and website. The front would be normal details

Target Market(s)

Wholesalers, grocers and distributors

Industry/Entity Type

Manufacture

Contact Information for Business Card

Business name: Prairie Lantern Popcorn
Phone: +1 555 308 4726
Email: Dale@prairielanternpopcorn.com
website: www.prairielanternpopcorn.com
Tag Line: "Kettle fresh, every time"
Name: Dale Whitcombe
Title: Founder/President

Requirements
Must have
• Either this design should be fun or clean and simple. I will let you show me your thougths.
Nice to have
• Anything that ties in the real Hwy Route 66.
• Colors might need to be red, white and blue incorporated.
Should not have
• Not be too busy.

```html
<!DOCTYPE html>
<html lang="en">
<head>
<meta charset="utf-8">
<title>Prairie Lantern Popcorn – Business Card</title>
<link href="https://fonts.googleapis.com/css2?family=Mulish:ital,wght@0,400;0,600;0,800;1,400&display=swap" rel="stylesheet">
<style>
  :root {
    --navy: #1b3168;
    --red: #d7202b;
    --paper: #ffffff;
    --backdrop: #e4e4e4;
    --ink: #2a3d6e;
    --muted: #555a66;
    --faint: #eef0f4;
  }
  * { box-sizing: border-box; margin: 0; padding: 0; }
  html, body {
    width: 1200px; height: 576px; overflow: hidden;
    background: var(--backdrop);
    font-family: "Mulish", sans-serif;
  }
  .canvas { position: relative; width: 1200px; height: 576px; }
  .card {
    position: absolute;
    background: var(--paper);
    border-radius: 6px;
    overflow: hidden;
  }

  /* Back side: brand + website */
  .card--back { left: 82px; top: 138px; width: 484px; height: 294px; }
  .brand-lockup {
    position: absolute; left: 0; right: 0; top: 80px;
    display: flex; flex-direction: column; align-items: center; gap: 14px;
  }
  .brand-dot { width: 34px; height: 34px; border-radius: 50%; background: var(--red); }
  .brand-name {
    color: var(--navy); font-weight: 800; font-size: 30px; line-height: 1.1;
    text-align: center; letter-spacing: 0.5px;
  }
  .web-rule {
    position: absolute; left: 0; right: 0; top: 257px;
    display: flex; align-items: center; justify-content: center; gap: 16px;
    font-size: 12px; font-weight: 600; color: var(--navy);
  }
  .web-rule .line { width: 44px; height: 2px; background: var(--navy); border-radius: 2px; }
  .web-rule .accent { color: var(--red); }

  /* Front side: contact details */
  .card--front { left: 602px; top: 138px; width: 480px; height: 291px; }
  .side-band {
    position: absolute; left: 0; top: 0; bottom: 0; width: 46px;
    background: var(--navy); border-right: 4px solid var(--red);
  }
  .tagline {
    position: absolute; left: 21px; top: 148px;
    transform: translate(-50%, -50%) rotate(-90deg);
    white-space: nowrap; color: #fff; font-size: 12.5px; letter-spacing: 0.3px;
  }
  .tagline b { font-weight: 800; }
  .brand-corner {
    position: absolute; left: 320px; top: 54px; width: 134px;
    color: var(--navy); font-weight: 800; font-size: 19px; line-height: 1.15;
    text-align: center;
  }
  .corner-decoration {
    position: absolute; left: 336px; top: 190px; width: 126px; height: 110px;
    border-radius: 60px 60px 0 0; background: var(--faint);
  }
  .person { position: absolute; left: 67px; top: 168px; }
  .person-name { color: var(--red); font-weight: 800; font-size: 16px; }
  .person-title { color: var(--muted); font-style: italic; font-size: 12.5px; margin-top: 1px; }
  .contacts {
    position: absolute; left: 67px; top: 215px; list-style: none;
    font-size: 13px; color: var(--ink);
  }
  .contacts li { display: flex; align-items: center; gap: 14px; height: 18px; }
  .contacts svg { width: 11px; height: 11px; fill: var(--red); flex: none; }
</style>
</head>
<body>
<main class="canvas">
  <section class="card card--back" aria-label="Card back">
    <div class="brand-lockup">
      <span class="brand-dot"></span>
      <p class="brand-name">Prairie Lantern<br>Popcorn</p>
    </div>
    <p class="web-rule">
      <span class="line"></span>
      <span>www.<span class="accent">prairielanternpopcorn</span>.com</span>
      <span class="line"></span>
    </p>
  </section>

  <section class="card card--front" aria-label="Card front">
    <div class="side-band"></div>
    <p class="tagline">"<b>Kettle</b> fresh, every time"</p>
    <div class="corner-decoration" role="img" aria-label="Faint popcorn cloud decoration"></div>
    <p class="brand-corner">Prairie Lantern<br>Popcorn</p>
    <div class="person">
      <p class="person-name">Dale Whitcombe</p>
      <p class="person-title">Founder/President</p>
    </div>
    <ul class="contacts">
      <li>
        <svg viewBox="0 0 12 12" aria-hidden="true"><path d="M1 3.5C1 2 2.5 1 6 1s5 1 5 2.5L9 4.5 8 3H4L3 4.5Z"/><rect x="2" y="5.5" width="8" height="5.5" rx="1"/></svg>
        <span>+1 555 308 4726</span>
      </li>
      <li>
        <svg viewBox="0 0 12 12" aria-hidden="true"><path d="M0.5 2.5h11v7h-11Z M1.5 3.2 6 6.6 10.5 3.2" stroke="#fff" stroke-width="0.8"/></svg>
        <span>Dale@prairielanternpopcorn.com</span>
      </li>
      <li>
        <svg viewBox="0 0 12 12" aria-hidden="true"><circle cx="6" cy="6" r="5.2"/><path d="M0.8 6h10.4M6 0.8c-2.5 3-2.5 7.4 0 10.4M6 0.8c2.5 3 2.5 7.4 0 10.4" stroke="#fff" stroke-width="0.8" fill="none"/></svg>
        <span>www.prairielanternpopcorn.com</span>
      </li>
    </ul>
  </section>
</main>
</body>
</html>
```